Velmarsh Group Webpage Design

We need a new website for our company. The company is Velmarsh Group Pty Ltd. We are in the business of Asbestos Removal; Demolition; Earthworks and Transport. We do not advertise and would like our website to be a reference point for our clients / potential clients and also to make our services known to those searching the internet for the services we offer. Some examples of the style of website we are after are:
http://www.quarnedemolition-example.com.au/
http://m.brintowerdemolitions-example.com.au/
http://www.fenwarddemolition-example.com.au
http://www.tolvik-example.com.au
http://www.ptrservices-example.com.au
http://www.steadfast-dismantling-example.com.au
We will need to work on content. Enclosed is an example. We also need to purchase the domain velmarshgroup-example.com.au and need to set up email accounts and ensure the website is mobile friendly. We have a company logo and have built our business on delivering professional, quality services on time. We would like the webpage to be simple, informative and professional - black and white / grey themed. We would also like to add a photo gallery etc later.

Industry/Entity Type

Construction

Coding

Coded - Design and coding required

Number of Pages Required

1 page

Colors
000000
fcfcfc
959595
dddddd

Requirements
Must have
• Information regarding the services we provide

```html
<!DOCTYPE html>
<html lang="en">
<head>
<meta charset="utf-8">
<title>Velmarsh Group</title>
<link href="https://fonts.googleapis.com/css2?family=Open+Sans:wght@300;400;600&family=Montserrat:wght@400;500;600;700&family=Roboto:wght@400;500&display=swap" rel="stylesheet">
<style>
:root{
  --black:#000000;
  --white:#fcfcfc;
  --grey:#959595;
  --light:#dddddd;
  --accent:#a0463c;
  --footer:#6a6a6a;
  --bar:#1c1c1c;
}
*{margin:0;padding:0;box-sizing:border-box}
html,body{width:1200px;height:2889px;overflow:hidden}
body{position:relative;background:var(--white);font-family:"Open Sans",sans-serif;color:var(--black)}
.abs{position:absolute}
/* hero */
.hero{left:0;top:0;width:1200px;height:657px;
  background:
    radial-gradient(ellipse 260px 220px at 640px 560px,rgba(225,110,50,.85),rgba(225,110,50,0)),
    radial-gradient(ellipse 200px 160px at 640px 120px,rgba(235,140,40,.7),rgba(235,140,40,0)),
    radial-gradient(ellipse 320px 300px at 1080px 460px,rgba(170,200,170,.8),rgba(170,200,170,0)),
    radial-gradient(ellipse 300px 200px at 150px 520px,rgba(190,110,90,.55),rgba(190,110,90,0)),
    linear-gradient(180deg,#e3e6ea 0%,#c6c9cc 45%,#8d8a86 100%)}
.logo{left:77px;top:18px;font-family:"Montserrat",sans-serif;font-weight:600;font-size:30px;letter-spacing:3px;color:var(--black)}
.nav{left:535px;top:0;height:83px;font-family:"Roboto",sans-serif;font-size:16px}
.nav a{color:var(--black);text-decoration:none;position:absolute;top:31px;white-space:nowrap}
.nav .active{left:0;top:0;width:89px;height:83px;background:var(--black);color:var(--white);display:flex;align-items:center;justify-content:center}
.hero-box{left:300px;top:241px;width:600px;height:227px;background:rgba(30,30,30,.78);text-align:center;color:var(--white);font-family:"Roboto",sans-serif}
.hero-box h1{font-family:"Montserrat",sans-serif;font-weight:600;font-size:25px;margin-top:50px;letter-spacing:.5px}
.hero-box hr{width:440px;margin:20px auto 0;border:0;border-top:1px solid var(--grey)}
.hero-box p{font-size:16px;line-height:25px;margin-top:24px}
.arrow{top:320px;width:50px;height:50px;border-radius:50%;background:var(--white);border:2px solid var(--black)}
/* about */
.about{left:0;top:657px;width:1200px;height:312px;background:var(--black);color:var(--white)}
.about h2{left:79px;top:64px;font-weight:300;font-size:52px;line-height:62px}
.divider-w{width:1px;background:#444}
.about p{left:453px;top:58px;width:650px;font-size:14.5px;line-height:29px;color:#b5b5b5}
.btn-white{left:451px;top:194px;width:165px;height:49px;background:var(--white);color:var(--black);font-family:"Roboto",sans-serif;font-size:16px;display:flex;align-items:center;justify-content:center}
/* hours */
.hours{left:0;top:969px;width:1200px;height:260px;
  background:
    radial-gradient(ellipse 300px 180px at 150px 200px,rgba(170,170,170,.6),rgba(170,170,170,0)),
    radial-gradient(ellipse 300px 180px at 1050px 80px,rgba(180,180,180,.6),rgba(180,180,180,0)),
    linear-gradient(90deg,#cfcfcf,#e2e2e2 50%,#d2d2d2);text-align:center}
.hours h2{width:100%;top:48px;font-weight:300;font-size:50px}
.hours hr{left:559px;top:132px;width:158px;border:0;border-top:2px solid #555}
.hours p{width:100%;top:153px;font-family:"Montserrat",sans-serif;font-weight:500;font-size:16.5px;line-height:28px}
/* services */
.section-title{font-weight:300;font-size:52px;line-height:64px;color:var(--black);text-align:center;width:320px}
.section-sub{font-family:"Montserrat",sans-serif;font-size:19px;line-height:24px;color:var(--light);letter-spacing:2px;text-align:center;width:320px}
.divider-g{width:1px;background:var(--light)}
.card{top:1290px;width:218px;height:187px;background:linear-gradient(180deg,#3c3632,#5a3c2e);border:2px solid #222;color:var(--white);text-align:center;font-family:"Roboto",sans-serif}
.card h3{font-family:"Montserrat",sans-serif;font-weight:700;font-size:20px;margin-top:30px}
.card hr{width:180px;margin:10px auto 0;border:0;border-top:1px solid #ccc}
.card p{font-size:14px;line-height:21px;margin-top:10px}
.card span{display:block;font-family:"Montserrat",sans-serif;font-weight:600;font-size:18px;margin-top:6px}
.photo-band{left:0;top:1541px;width:1200px;height:314px;
  background:
    radial-gradient(ellipse 160px 200px at 300px 200px,rgba(230,180,40,.75),rgba(230,180,40,0)),
    radial-gradient(ellipse 220px 90px at 1050px 200px,rgba(60,110,50,.8),rgba(60,110,50,0)),
    radial-gradient(ellipse 200px 80px at 120px 200px,rgba(70,110,60,.7),rgba(70,110,60,0)),
    linear-gradient(180deg,#3f78bf 0%,#8fb6e0 40%,#b9c4cc 58%,#8c8c86 75%,#a89a88 100%)}
.tile{width:171px;height:118px}
/* contact */
.contact{left:0;top:2177px;width:1200px;height:433px;background:linear-gradient(180deg,#2d3238,#3b3f44 60%,#2b2e31)}
.contact h2{width:100%;top:34px;text-align:center;font-weight:300;font-size:52px;color:var(--white)}
.label{font-family:"Roboto",sans-serif;font-size:14px;color:var(--white)}
.field{height:36px;background:rgba(220,220,220,.35)}
.field i{position:absolute;left:0;top:0;width:36px;height:36px;background:var(--white)}
.send{left:510px;top:333px;width:178px;height:50px;background:var(--white);font-family:"Montserrat",sans-serif;font-weight:600;font-size:16px;display:flex;align-items:center;justify-content:center}
/* footer */
.footer{left:0;top:2610px;width:1200px;height:225px;background:var(--footer);color:var(--white)}
.footer h4{font-family:"Roboto",sans-serif;font-weight:500;font-size:16px}
.footer h4 b{color:var(--black);font-weight:500}
.row{font-family:"Roboto",sans-serif;font-size:13px;display:flex;align-items:center}
.row svg{width:16px;height:16px;margin-right:19px;fill:#bdbdbd}
.map{left:747px;top:50px;width:376px;height:125px;border:2px solid #ddd;
  background:
    radial-gradient(ellipse 120px 40px at 230px 70px,rgba(120,180,110,.55),rgba(120,180,110,0)),
    radial-gradient(ellipse 90px 60px at 60px 40px,rgba(240,200,90,.5),rgba(240,200,90,0)),
    linear-gradient(135deg,#ece4cc,#dfe3c8 50%,#ead9b4)}
.bar{left:0;top:2835px;width:1200px;height:54px;background:var(--bar);color:var(--white);font-family:"Roboto",sans-serif;font-size:13px}
.bar .copy{left:79px;top:18px}
.bar .copy em{font-style:normal;color:#c0493a}
.social{top:18px;width:18px;height:18px;border-radius:50%;background:var(--white)}
</style>
</head>
<body>

<header class="abs hero" role="img" aria-label="Photo of a construction worker in a hard hat and safety vest on a worksite"></header>
<div class="abs logo">VELMARSH GROUP</div>
<nav class="abs nav">
  <a class="active">Home</a>
  <a style="left:118px">About</a>
  <a style="left:205px">Services</a>
  <a style="left:305px">Gallary</a>
  <a style="left:401px">Projects</a>
  <a style="left:497px">contact us</a>
</nav>
<div class="abs hero-box">
  <h1>Transport &nbsp;-&nbsp; Demolition &nbsp;-&nbsp; Earthmoving</h1>
  <hr>
  <p>Velmarsh Transport and Demolition is built on core values of Service,<br>Safety and Environment.</p>
</div>
<svg class="abs arrow" style="left:12px" viewBox="0 0 50 50"><path d="M25 16l-9 9 9 9M34 16l-9 9 9 9" fill="none" stroke="#000" stroke-width="4"/></svg>
<svg class="abs arrow" style="left:1136px" viewBox="0 0 50 50"><path d="M16 16l9 9-9 9M25 16l9 9-9 9" fill="none" stroke="#000" stroke-width="4"/></svg>

<section class="abs about">
  <h2 class="abs">Know More<br>About US</h2>
  <svg class="abs" style="left:182px;top:203px" width="58" height="52" viewBox="0 0 58 52" fill="#fcfcfc"><circle cx="29" cy="13" r="10"/><circle cx="11" cy="18" r="7"/><circle cx="47" cy="18" r="7"/><path d="M13 50c0-14 7-24 16-24s16 10 16 24z"/><path d="M0 46c0-10 5-17 11-17 3 0 5 1 7 3-4 4-6 9-6 14z"/><path d="M58 46c0-10-5-17-11-17-3 0-5 1-7 3 4 4 6 9 6 14z"/></svg>
  <div class="abs divider-w" style="left:399px;top:42px;height:227px"></div>
  <p class="abs">Velmarsh Transport Pty Ltd was established by Director Daniel Velmarsh in 2002 with a focus providing services within the transport industry. Over time the company has developed and expanded to include the provision of Earthworks and Demolition. Daniel has over 10 years' experience working at all levels within these industries focusing primarily.</p>
  <div class="abs btn-white">READ MORE</div>
</section>

<section class="abs hours" role="img" aria-label="Faded photo of crushed rubble behind the section heading">
  <h2 class="abs">Hours of Operation</h2>
  <hr class="abs">
  <p class="abs">Velmarsh Transport and Demolition operate Monday to Saturday. Hours of operation are<br>generally assessed and implemented to meet the needs of each individual project.</p>
</section>

<section>
  <h2 class="abs section-title" style="left:67px;top:1286px">Our Services</h2>
  <div class="abs section-sub" style="left:67px;top:1351px">What We Do</div>
  <svg class="abs" style="left:205px;top:1402px" width="56" height="50" viewBox="0 0 56 50" fill="#a0463c"><circle cx="20" cy="28" r="14"/><g stroke="#a0463c" stroke-width="6"><path d="M20 8v40M0 28h40M6 14l28 28M34 14L6 42"/></g><circle cx="20" cy="28" r="5" fill="#fcfcfc"/><circle cx="44" cy="12" r="8"/><g stroke="#a0463c" stroke-width="4"><path d="M44 0v24M32 12h24M36 4l16 16M52 4L36 20"/></g><circle cx="44" cy="12" r="3" fill="#fcfcfc"/><circle cx="44" cy="40" r="7"/><g stroke="#a0463c" stroke-width="4"><path d="M44 30v20M34 40h20"/></g><circle cx="44" cy="40" r="2.5" fill="#fcfcfc"/></svg>
  <div class="abs divider-g" style="left:400px;top:1271px;height:227px"></div>
  <div class="abs card" style="left:426px" role="img" aria-label="Demolition service tile with a demolition site photo">
    <h3>Demolition</h3><hr><p>Velmarsh Transport and<br>Demolition provide.</p><span>READ MORE</span>
  </div>
  <div class="abs card" style="left:665px" role="img" aria-label="Earthworks service tile with an excavator photo">
    <h3>Earthworks</h3><hr><p>Velmarsh Transport and<br>Demolition possess.</p><span>READ MORE</span>
  </div>
  <div class="abs card" style="left:903px" role="img" aria-label="Asbestos service tile with a roof photo">
    <h3>Asbestos</h3><hr><p>Asbestos is a naturally<br>occurring silicate.</p><span>READ MORE</span>
  </div>
</section>

<div class="abs photo-band" role="img" aria-label="Photo of excavators breaking up a city road under a blue sky"></div>

<section>
  <h2 class="abs section-title" style="left:52px;top:1938px">Our Gallary</h2>
  <div class="abs section-sub" style="left:52px;top:2002px">Project Images</div>
  <svg class="abs" style="left:183px;top:2048px" width="66" height="52" viewBox="0 0 66 52"><rect x="8" y="0" width="56" height="42" rx="3" fill="#a0463c"/><rect x="1" y="8" width="56" height="42" rx="3" fill="#fcfcfc" stroke="#a0463c" stroke-width="3"/><rect x="6" y="13" width="46" height="32" fill="#a0463c"/><circle cx="16" cy="21" r="4" fill="#fcfcfc"/><path d="M8 43l13-12 8 7 10-12 12 17z" fill="#fcfcfc"/></svg>
  <div class="abs divider-g" style="left:399px;top:1907px;height:227px"></div>
  <div class="abs tile" style="left:435px;top:1899px;background:linear-gradient(135deg,#9fb8d0,#d8c46a)" role="img" aria-label="Gallery photo of engineers reviewing plans"></div>
  <div class="abs tile" style="left:607px;top:1899px;background:linear-gradient(135deg,#1d2a3c,#4a5a6a)" role="img" aria-label="Gallery photo of a crane at dusk"></div>
  <div class="abs tile" style="left:778px;top:1899px;background:linear-gradient(135deg,#cfd9e4,#8fa3b5)" role="img" aria-label="Gallery photo of a tablet showing a building"></div>
  <div class="abs tile" style="left:950px;top:1899px;background:linear-gradient(135deg,#e2c28a,#6c7a88)" role="img" aria-label="Gallery photo of a site supervisor at sunset"></div>
  <div class="abs tile" style="left:435px;top:2017px;background:linear-gradient(135deg,#e8dccb,#9c7a58)" role="img" aria-label="Gallery photo of an attic renovation"></div>
  <div class="abs tile" style="left:607px;top:2017px;background:linear-gradient(135deg,#7fa2c0,#b86a3e)" role="img" aria-label="Gallery photo of workers on a tiled roof"></div>
  <div class="abs tile" style="left:778px;top:2017px;background:linear-gradient(135deg,#c0d4e6,#b25a34)" role="img" aria-label="Gallery photo of roof framing"></div>
  <div class="abs tile" style="left:950px;top:2017px;background:linear-gradient(135deg,#d7b08a,#a45a36)" role="img" aria-label="Gallery photo of a roofer laying tiles"></div>
  <svg class="abs" style="left:681px;top:1950px" width="22" height="22" viewBox="0 0 22 22"><circle cx="9" cy="9" r="6.5" fill="none" stroke="#fcfcfc" stroke-width="3"/><path d="M14 14l6 6" stroke="#fcfcfc" stroke-width="3.5"/></svg>
</section>

<section class="abs contact" role="img" aria-label="Dark photo of a city skyline behind the contact form">
  <h2 class="abs">Keep In Touch</h2>
  <div class="abs label" style="left:231px;top:126px">Name</div>
  <div class="abs label" style="left:607px;top:126px">Email Id</div>
  <div class="abs field" style="left:231px;top:148px;width:364px"><i></i></div>
  <div class="abs field" style="left:605px;top:148px;width:364px"><i></i></div>
  <svg class="abs" style="left:239px;top:156px" width="20" height="20" viewBox="0 0 20 20"><circle cx="10" cy="6" r="5" fill="#000"/><path d="M1 20c0-6 4-9 9-9s9 3 9 9z" fill="#000"/></svg>
  <svg class="abs" style="left:613px;top:158px" width="20" height="16" viewBox="0 0 20 16"><rect width="20" height="16" fill="#000"/><path d="M1 2l9 7 9-7" fill="none" stroke="#fcfcfc" stroke-width="1.6"/></svg>
  <div class="abs label" style="left:231px;top:189px">Message</div>
  <div class="abs field" style="left:231px;top:211px;width:738px;height:100px"></div>
  <div class="abs send">SEND</div>
</section>

<footer class="abs footer">
  <h4 class="abs" style="left:79px;top:45px">Daniel Velmarsh <b>(Direcor)</b></h4>
  <div class="abs row" style="left:79px;top:92px"><svg viewBox="0 0 16 16"><path d="M8 0a5.5 5.5 0 0 0-5.5 5.5C2.5 10 8 16 8 16s5.5-6 5.5-10.5A5.5 5.5 0 0 0 8 0zm0 8a2.5 2.5 0 1 1 0-5 2.5 2.5 0 0 1 0 5z"/></svg>PO Box 512 HARLOWVALE QLD 4399</div>
  <div class="abs row" style="left:79px;top:123px"><svg viewBox="0 0 16 16"><rect y="2" width="16" height="12"/><path d="M1 3l7 6 7-6" fill="none" stroke="#6a6a6a" stroke-width="1.4"/></svg>office@velmarshgroup-example.com.au</div>
  <div class="abs row" style="left:79px;top:159px"><svg viewBox="0 0 16 16"><path d="M3 1l3 3-2 2c1 2 3 4 5 5l2-2 3 3-2 3C7 15 1 9 1 3z"/></svg>0400 000 111</div>
  <h4 class="abs" style="left:443px;top:45px">Megan Tolley <b>(Administrator)</b></h4>
  <div class="abs row" style="left:443px;top:92px"><svg viewBox="0 0 16 16"><path d="M8 0a5.5 5.5 0 0 0-5.5 5.5C2.5 10 8 16 8 16s5.5-6 5.5-10.5A5.5 5.5 0 0 0 8 0zm0 8a2.5 2.5 0 1 1 0-5 2.5 2.5 0 0 1 0 5z"/></svg>PO Box 512 HARLOWVALE QLD 4399</div>
  <div class="abs row" style="left:443px;top:123px"><svg viewBox="0 0 16 16"><rect y="2" width="16" height="12"/><path d="M1 3l7 6 7-6" fill="none" stroke="#6a6a6a" stroke-width="1.4"/></svg>office@velmarshgroup-example.com.au</div>
  <div class="abs row" style="left:443px;top:159px"><svg viewBox="0 0 16 16"><path d="M3 1l3 3-2 2c1 2 3 4 5 5l2-2 3 3-2 3C7 15 1 9 1 3z"/></svg>0400 000 222</div>
  <div class="abs map" role="img" aria-label="Street map showing the office location"></div>
</footer>

<div class="abs bar">
  <div class="abs copy">© <em>VELMARSH</em> - 2015. All Rights Reserved.</div>
  <div class="abs social" style="left:1018px" aria-label="Social link"></div>
  <div class="abs social" style="left:1060px;background:#c0493a" aria-label="Social link"></div>
  <div class="abs social" style="left:1102px" aria-label="Social link"></div>
</div>

</body>
</html>
```